Non Profit Company Looking For New Website

The website for Fernvale Quillstone Heritage Society should offer the viewer beautiful photos that inspire condifence and joy and tap into our love of horses.

We would like to see a website that displays trust, quality and confidence. Needs to be responsive and mobile friendly for all browsers and coded for both Android & IOS.

READ ATTACHED WEBSITE TEMPLATE FOR COMPLETE DETAILS ON WHAT WE ARE LOOKING FOR.

Looking for recommmendations if we should use WordPress/WooCommerce for site or Wordpress with Shopify Plug in or just Shopify.

Must be both desktop and mobile friendly with fast page load speed. Need the ability to edit ourselves.

Industry/Entity Type

Non Profit

Coding

Coded - Design and coding required

Number of Pages Required

5+ page

Requirements
Must have
• We would like to see a website that displays trust, quality and confidence. Needs to be responsive and mobile friendly for all browsers and coded for both Android & IOS.

Looking for recommendations if we should use WordPress/WooCommerce for site or Wordpress with Shopify Plug in or just Shopify.

Logo Colour:
Pantone 7621 C

READ TEMPLATE THAT IS ATTACHED
Nice to have
• Like look of this website as a sample:
https://www.quellbrimtorva.com/

Another similar non profit organization
https://pellaworthcindle.com/

```html
<!DOCTYPE html>
<html lang="en">
<head>
<meta charset="utf-8">
<title>Fernvale Quillstone Heritage Society</title>
<link href="https://fonts.googleapis.com/css2?family=Lora:wght@500;700&family=Roboto:wght@300;400;500;700&display=swap" rel="stylesheet">
<style>
:root{
  --red:#b51f2c;
  --red-dark:#9c1a25;
  --ink:#1d1d1d;
  --body:#555;
  --line:#e4e4e4;
  --white:#fff;
}
*{box-sizing:border-box;margin:0;padding:0}
html,body{width:1200px;height:3002px;overflow:hidden;background:var(--white)}
body{position:relative;font-family:'Roboto',sans-serif;color:var(--ink)}
.abs{position:absolute}
.serif{font-family:'Lora',serif}
.btn{position:absolute;display:flex;align-items:center;justify-content:center;background:var(--red);color:var(--white);font-weight:700;font-size:15px;border-radius:3px;text-transform:uppercase;letter-spacing:.1px}
.btn-outline{background:transparent;border:2px solid var(--red);color:var(--red)}

/* header */
.site-header{position:absolute;left:0;top:0;width:1200px;height:98px;background:var(--white);border-bottom:1px solid var(--line)}
.brand{position:absolute;left:104px;top:22px;width:130px;display:flex;align-items:center;gap:8px;font-family:'Lora',serif;font-weight:700;color:var(--red);font-size:14px;line-height:17px}
.brand-dot{width:14px;height:14px;border-radius:50%;background:var(--red);flex:none}
.main-nav{position:absolute;left:370px;top:41px;display:flex;gap:29px;font-size:15px;font-weight:500}
.main-nav a{color:var(--ink);text-decoration:none}
.main-nav a.active{color:var(--red)}

/* hero */
.hero{position:absolute;left:0;top:98px;width:1200px;height:557px;background:linear-gradient(180deg,#8fa6a4 0%,#b9b58a 35%,#c6b25a 60%,#7f8a3a 85%,#5c6a2c 100%)}
.hero-horse{position:absolute;left:110px;top:30px;width:500px;height:527px;background:radial-gradient(ellipse at 50% 50%,rgba(150,70,30,.85),rgba(150,70,30,0) 70%)}
.hero-title{position:absolute;left:600px;top:178px;width:560px;font-family:'Lora',serif;font-size:32px;line-height:40px;font-weight:500;color:var(--white);text-transform:uppercase}

/* intro */
.pillar-icons{position:absolute;top:736px;left:422px;display:flex;gap:70px}
.pillar-icons span{width:64px;height:74px;background:var(--red);opacity:.9;border-radius:10px 30px 6px 6px}
.section-title{position:absolute;left:0;width:1200px;text-align:center;font-family:'Lora',serif;font-weight:700;color:var(--red);text-transform:uppercase}
.rule{position:absolute;left:579px;width:42px;height:2px;background:var(--red)}
.intro-sub{position:absolute;left:0;top:892px;width:1200px;text-align:center;font-family:'Lora',serif;font-weight:700;font-size:21px}
.intro-lead{position:absolute;left:0;top:938px;width:1200px;text-align:center;font-size:14.5px;font-weight:300;color:var(--body)}
.intro-body{position:absolute;left:200px;top:971px;width:800px;text-align:center;font-size:15.5px;line-height:27.5px;font-weight:300;color:var(--body)}
.divider{position:absolute;left:0;top:1223px;width:1200px;height:1px;background:var(--line)}

/* adopt */
.adopt-lead{position:absolute;left:0;top:1357px;width:1200px;text-align:center;font-size:15.5px;font-weight:300;color:var(--body)}
.horse-tile{position:absolute;width:316px;height:245px;background:var(--white);padding:4px;box-shadow:0 2px 8px rgba(0,0,0,.12)}
.horse-tile .photo{width:100%;height:100%}
.tile-feature{box-shadow:0 8px 22px rgba(0,0,0,.25)}
.feature-card{position:relative;width:100%;height:100%;background:linear-gradient(180deg,#c8555d 0%,#c23442 45%,#c0283a 100%);color:var(--white)}
.feature-name{position:absolute;left:0;top:84px;width:100%;text-align:center;font-weight:500;font-size:16.5px;text-transform:uppercase}
.feature-line{position:absolute;left:0;top:112px;width:100%;height:1px;background:rgba(255,255,255,.55)}
.feature-specs{position:absolute;left:12px;top:132px;font-size:11.5px;line-height:14px}
.spec-fee{position:absolute;left:0;top:0;font-weight:700}
.spec-fee-val{position:absolute;left:36px;top:-3px;width:46px}
.spec-keys{position:absolute;left:96px;top:0;font-weight:700;line-height:21px;white-space:nowrap}
.spec-vals{position:absolute;left:161px;top:0;line-height:21px;white-space:nowrap}
.feature-btn{position:absolute;left:210px;width:94px;height:44px;border:2px solid var(--white);display:flex;align-items:center;justify-content:center;text-align:center;font-size:10px;font-weight:700;line-height:12px;text-transform:uppercase}

/* give band */
.give{position:absolute;left:0;top:2117px;width:1200px;height:371px;background:linear-gradient(90deg,#6f5a3a 0%,#8a7a55 25%,#6e7450 45%,#55613f 70%,#4a5637 100%)}
.give-scene{position:absolute;left:0;top:0;width:640px;height:371px;background:radial-gradient(ellipse at 55% 60%,rgba(160,95,50,.6),rgba(160,95,50,0) 65%)}
.give-title{position:absolute;left:635px;top:55px;font-family:'Lora',serif;font-weight:700;font-size:25px;color:var(--white);text-transform:uppercase}
.give-rule{position:absolute;left:636px;top:108px;width:42px;height:2px;background:var(--white)}
.give-text{position:absolute;left:636px;top:124px;width:460px;font-size:15.5px;line-height:27.5px;color:var(--white);font-weight:300}

/* contact */
.contact{position:absolute;left:0;top:2488px;width:1200px;height:457px;background:linear-gradient(180deg,#fff 0%,#fbf9f8 100%)}
.contact-title{position:absolute;left:0;top:71px;width:1200px;text-align:center;font-family:'Lora',serif;font-weight:500;font-size:26px;text-transform:uppercase}
.info-icon{position:absolute;left:103px;width:51px;height:51px;border-radius:50%;background:var(--white);box-shadow:0 2px 10px rgba(0,0,0,.12);display:flex;align-items:center;justify-content:center}
.info-label{position:absolute;left:177px;font-size:14px;font-weight:700;text-transform:uppercase}
.info-text{position:absolute;left:177px;font-size:14.5px;line-height:23px;color:var(--body);font-weight:300}
.field{position:absolute;background:var(--white);border:1px solid #d8d8d8;font-size:14px;color:#777;padding:0 20px;display:flex;align-items:center;justify-content:space-between}
.field-area{align-items:flex-start;padding-top:18px}

.site-footer{position:absolute;left:0;top:2945px;width:1200px;height:57px;background:var(--red);color:var(--white);font-size:15.5px;display:flex;align-items:center;justify-content:center}
</style>
</head>
<body>

<header class="site-header">
  <div class="brand"><span class="brand-dot"></span><span>Fernvale Quillstone Heritage</span></div>
  <nav class="main-nav">
    <a class="active" href="#">HOME</a><a href="#">ABOUT</a><a href="#">ADOPT</a><a href="#">HORSES</a><a href="#">DONATE</a><a href="#">SHOP</a><a href="#">CONTACT</a>
  </nav>
  <a class="btn" style="left:953px;top:28px;width:130px;height:44px">Donate Now</a>
</header>

<section class="hero" role="img" aria-label="Chestnut horse with flowing mane standing in a sunlit meadow of yellow wildflowers">
  <div class="hero-horse"></div>
  <h1 class="hero-title">We support &amp; develop retired thoroughbred racehorses for their next chapter in life</h1>
  <a class="btn" style="left:601px;top:323px;width:203px;height:49px;font-size:14px">Adopt a Thoroughbred</a>
  <a class="btn btn-outline" style="left:826px;top:323px;width:152px;height:49px;font-size:14px">Donate Now</a>
</section>

<section class="intro">
  <div class="pillar-icons">
    <span role="img" aria-label="Standing horse silhouette"></span>
    <span role="img" aria-label="Horse and rider silhouette"></span>
    <span role="img" aria-label="Galloping horse silhouette"></span>
  </div>
  <h2 class="section-title" style="top:822px;font-size:25px">Retire. Retrain. Rehome.</h2>
  <div class="rule" style="top:871px"></div>
  <h3 class="intro-sub">What is Thoroughbred Aftercare?</h3>
  <p class="intro-lead">Fernvale Quillstone Heritage Society (FQH) is a registered not-for-profit organization in Fernvale.</p>
  <p class="intro-body">The health, safety and welfare of our equine athletes does not end at the finish line, and retirement and aftercare are critical to the success of the racing industry.Aftercare is the safe placement of racehorses after their careers as racehorse are completed. Some horses might retire to the breeding shed or broodmare bands, while others are retrained for second careers.</p>
  <a class="btn" style="left:498px;top:1109px;width:204px;height:48px;font-size:14.5px">Learn More About Us</a>
</section>

<div class="divider"></div>

<section class="adopt">
  <h2 class="section-title" style="top:1278px;font-size:25px">Adopt a Horse</h2>
  <div class="rule" style="top:1323px"></div>
  <p class="adopt-lead">Fernvale Quillstone Heritage is committed to helping match you with the perfect horse.</p>

  <div class="horse-tile" style="left:112px;top:1417px"><div class="photo" role="img" aria-label="Chestnut horse standing on green grass before trees" style="background:linear-gradient(180deg,#3f7a2e,#6c9a3e 55%,#8fb24a)"></div></div>
  <div class="horse-tile" style="left:443px;top:1417px"><div class="photo" role="img" aria-label="Bay horse in a yellow flower field under blue sky" style="background:linear-gradient(180deg,#a9c8e6,#d8dc7a 45%,#e3d24a 70%,#b9b43c)"></div></div>
  <div class="horse-tile" style="left:772px;top:1417px"><div class="photo" role="img" aria-label="Dark bay horse on a pasture with trees" style="background:linear-gradient(180deg,#b8d4e8,#5b7f3b 40%,#6f9b3f 75%,#86b04a)"></div></div>
  <div class="horse-tile" style="left:112px;top:1675px"><div class="photo" role="img" aria-label="Saddled horse beside a metal fence on a green hillside" style="background:linear-gradient(180deg,#7a9a4a,#6f8f3c 50%,#5a6a3a)"></div></div>
  <div class="horse-tile tile-feature" style="left:443px;top:1675px">
    <div class="feature-card" role="img" aria-label="Featured horse card with chestnut horse photo behind a red tint">
      <div class="feature-name">Marrowdale Spark</div>
      <div class="feature-line"></div>
      <div class="feature-specs">
        <span class="spec-fee">FEE</span>
        <span class="spec-fee-val">$1,000 NOW $800 UNTIL 5/31</span>
        <span class="spec-keys">HEIGHT<br>BIRTH YR<br>COLOR<br>GENDER<br>LOC</span>
        <span class="spec-vals">16.1<br>2007<br>Bay<br>Gelding<br>USA</span>
      </div>
      <div class="feature-btn" style="top:134px">View more on this horse</div>
      <div class="feature-btn" style="top:184px">View all horses</div>
    </div>
  </div>
  <div class="horse-tile" style="left:772px;top:1675px"><div class="photo" role="img" aria-label="Chestnut horse standing in front of leafy trees" style="background:linear-gradient(180deg,#6b8a3a,#4c6a2c 50%,#7d8f44)"></div></div>

  <a class="btn" style="left:541px;top:1981px;width:117px;height:44px">Adopt Now</a>
</section>

<section class="give" role="img" aria-label="Woman kneeling beside a grazing chestnut horse in a daisy meadow">
  <div class="give-scene"></div>
  <h2 class="give-title">Make a Difference</h2>
  <div class="give-rule"></div>
  <p class="give-text">Lorem ipsum dolor sit amet, consectetur adipiscing elit, sed do eiusmod tempor incididunt ut labore et dolore magna aliqua. Ut enim ad minim veniam, quis nostrud exercitation ullamco laboris nisi ut aliquip ex ea commodo consequat.</p>
  <a class="btn" style="left:636px;top:263px;width:177px;height:48px;font-size:14.5px">More Ways to Give</a>
</section>

<section class="contact">
  <h2 class="contact-title">Contact Us</h2>

  <div class="info-icon" style="top:143px"><svg width="22" height="24" viewBox="0 0 24 24" fill="none" stroke="#b51f2c" stroke-width="1.6"><path d="M12 22s7-7 7-12a7 7 0 0 0-14 0c0 5 7 12 7 12z"/><circle cx="12" cy="10" r="2.6"/></svg></div>
  <div class="info-label" style="top:166px">Location</div>
  <div class="info-text" style="top:194px">47 Kestrelwood Lane, Brindlemoor,<br>Oakhaven</div>

  <div class="info-icon" style="top:261px"><svg width="24" height="22" viewBox="0 0 24 22" fill="none" stroke="#b51f2c" stroke-width="1.6"><rect x="2" y="6" width="20" height="14"/><path d="M2 6l10 8 10-8"/><path d="M6 6V2h12v4"/></svg></div>
  <div class="info-label" style="top:264px">Email Us</div>
  <div class="info-text" style="top:290px">info@fernvalequill.org</div>

  <div class="info-icon" style="top:334px"><svg width="24" height="24" viewBox="0 0 24 24" fill="none" stroke="#b51f2c" stroke-width="1.6"><path d="M5 3h4l2 5-3 2a11 11 0 0 0 6 6l2-3 5 2v4a2 2 0 0 1-2 2A17 17 0 0 1 3 5a2 2 0 0 1 2-2z"/><path d="M15 3a6 6 0 0 1 6 6M15 7a2 2 0 0 1 2 2"/></svg></div>
  <div class="info-label" style="top:338px">Contact Us</div>
  <div class="info-text" style="top:364px">1 555 014 2277</div>

  <div class="field" style="left:407px;top:149px;width:321px;height:49px">Your Name<svg width="14" height="14" viewBox="0 0 16 16" fill="none" stroke="#555" stroke-width="1.4"><circle cx="8" cy="8" r="7"/><circle cx="8" cy="6.5" r="2.3"/><path d="M3.5 13a5 5 0 0 1 9 0"/></svg></div>
  <div class="field" style="left:407px;top:209px;width:321px;height:49px">Email Address<svg width="14" height="12" viewBox="0 0 16 12" fill="none" stroke="#555" stroke-width="1.4"><rect x="1" y="1" width="14" height="10"/><path d="M1 1l7 6 7-6"/></svg></div>
  <div class="field" style="left:407px;top:269px;width:321px;height:49px">Phone No<svg width="13" height="13" viewBox="0 0 16 16" fill="#555"><path d="M3 1h3l1.5 4-2 1.5a9 9 0 0 0 4 4l1.5-2 4 1.5v3a1.5 1.5 0 0 1-1.5 1.5A13 13 0 0 1 1.5 2.5 1.5 1.5 0 0 1 3 1z"/></svg></div>
  <div class="field" style="left:407px;top:329px;width:321px;height:49px">Address<svg width="11" height="14" viewBox="0 0 12 16" fill="#555"><path d="M6 0a6 6 0 0 0-6 6c0 4 6 10 6 10s6-6 6-10a6 6 0 0 0-6-6zm0 8.3A2.3 2.3 0 1 1 6 3.7a2.3 2.3 0 0 1 0 4.6z"/></svg></div>
  <div class="field field-area" style="left:755px;top:149px;width:333px;height:169px">Message<svg width="15" height="13" viewBox="0 0 16 14" fill="none" stroke="#555" stroke-width="1.3"><path d="M2 2h9v6H6l-3 2V8H2z"/><path d="M11 5h3v6h-1v2l-3-2H7V8"/></svg></div>
  <a class="btn" style="left:755px;top:329px;width:138px;height:49px;font-size:14.5px;gap:10px">Submit Now<svg width="14" height="14" viewBox="0 0 16 16"><circle cx="8" cy="8" r="8" fill="#fff"/><path d="M6.5 4.5L10 8l-3.5 3.5" stroke="#b51f2c" stroke-width="2" fill="none"/></svg></a>
</section>

<footer class="site-footer">© 2021 Fernvale Quillstone Heritage. All Rights Reserved</footer>

</body>
</html>
```